Wordpress Web Design & Coding for velcorahealth.ca

We need a website for a new investment company that is visually grabbing and vibrant. We would like to see a web page that displays trust, growth and confidence. Needs to be responsive and mobile friendly for all browsers and coded for both Android & IOS.

Open to the number of pages and menu items. I selected 4 but if you feel the layout would work better with less I am open to this. Need to sell the people (management team/related businesses) and then show where the invested money will be going (upcoming projects).

Company Info:

Vel Cora is an investment company put together by a group of seasoned business professionals who have come together to combine decades of success in the real estate development, management, financing and medical services. The company will be a full service company offering turn key solutions for medical professionals.

Vel-Cora will focus on providing a full range of services via a group of distinct companies to deliver newly emerging needs of the medical community. The end goal will be to create complete solutions for individuals in the medical community. Our group has experience and success with the conceptualization, construction and financing of medical and dental clinic spaces. Vel-Cora Solutions will be established to accommodate all areas of the development and creation of clinics for medical professionals from building construction to equipment financing and administrations.

You can mention these companies and take photos from their websites. You can also use stock photos.

Our construction partner:
https://318bld.com/projects/

Our equipment leasing partner:
https://www.norvixa.com/

Our Management Team and medical partners

Gil Parish
https://www.ourfirmstance.ca/

Dietmar Vellasquin
https://www.gshdentalservices.com/about-us

PROPOSED PROJECTS (see attachment for details)
Pinegrove Business Park
Holtmere Business Park
Mt. Corwin Ridge Professional

Target Market(s)

Investors

Industry/Entity Type

Investment

Coding

Coded - Design and coding required

Number of Pages Required

4 page

Font styles to use
Sans Serif

Requirements
Must have
• Wordpress – must be both desktop and mobile friendly with fast page load speed
Ability to edit after ourselves in Wordpress
Attractive home page with logo etc.
Logo colours are: for the blue the pantone color is #0355a3
and for the green is #8cc63f

Sections, about us, what we do/services we provide, contact us

```html
<!DOCTYPE html>
<html lang="en">
<head>
<meta charset="utf-8">
<title>Vel-Cora Solutions</title>
<link rel="stylesheet" href="https://fonts.googleapis.com/css2?family=Poppins:wght@400;500;600;700&family=Lato:wght@400;700&display=swap">
<style>
:root{
  --blue:#123f8f;
  --blue-dark:#0e3479;
  --brand:#0355a3;
  --green:#8cc63f;
  --ink:#222;
  --muted:#666;
  --field:#e4e4e4;
  --black:#000;
  --white:#fff;
}
*{box-sizing:border-box;margin:0;padding:0}
html,body{width:1200px;height:2733px;overflow:hidden}
body{position:relative;background:var(--white);font-family:'Lato',sans-serif;color:var(--ink)}
.abs{position:absolute}
.topbar{left:0;top:0;width:1200px;height:7px;background:var(--blue)}
.topbar::before{content:"";position:absolute;left:0;top:0;width:600px;height:7px;background:var(--green)}
.brand{display:flex;align-items:center;gap:8px;font-family:'Poppins',sans-serif;font-weight:700;color:var(--brand);line-height:1.05}
.brand-mark{width:18px;height:18px;background:var(--brand);flex:none}
.site-brand{left:111px;top:36px;font-size:20px}
.nav{left:404px;top:46px;display:flex;gap:0;font-family:'Poppins',sans-serif;font-size:18px;color:#222}
.nav a{color:inherit;text-decoration:none;position:absolute;white-space:nowrap}
.nav a.active{color:var(--brand)}
.nav a.active::after{content:"";position:absolute;left:0;right:0;bottom:-6px;height:2px;background:var(--brand)}
.phone-chip{left:919px;top:43px;display:flex;align-items:center;gap:15px;font-family:'Poppins',sans-serif;font-weight:600;font-size:18px}
.circle-icon{width:34px;height:34px;border-radius:50%;background:var(--blue-dark);display:flex;align-items:center;justify-content:center}
.hero{left:0;top:104px;width:1200px;height:557px;background:radial-gradient(ellipse 420px 300px at 900px 200px,#1d8a6d 0%,rgba(20,90,80,.6) 45%,rgba(15,50,55,0) 75%),linear-gradient(100deg,#0f2f33 0%,#123c40 45%,#15504f 70%,#0e2a33 100%)}
.hero-title{left:111px;top:245px;font-family:'Poppins',sans-serif;font-weight:500;font-size:62px;color:var(--white);letter-spacing:-.5px}
.hero-text{left:111px;top:332px;width:560px;font-size:15px;line-height:26px;color:var(--white)}
.btn{display:flex;align-items:center;justify-content:center;background:var(--blue);color:var(--white);font-family:'Poppins',sans-serif;font-weight:700;border-radius:4px}
.hero-btn{left:111px;top:432px;width:161px;height:62px;font-size:18px}
.dots{left:580px;top:610px;display:flex;gap:4px}
.dots span{width:12px;height:12px;border-radius:50%;border:1.5px solid var(--white)}
.dots span.on{background:var(--white)}
.partner{top:709px;width:181px;height:76px;background:var(--white);box-shadow:0 2px 8px rgba(0,0,0,.22);display:flex;align-items:center;justify-content:center;font-family:'Poppins',sans-serif;font-weight:600;font-size:15px;color:#333;text-align:center}
.about-photo{left:0;top:886px;width:515px;height:343px;background:linear-gradient(135deg,#c9d6e4 0%,#9fb2c8 50%,#6e88a8 100%)}
.h2{font-family:'Poppins',sans-serif;font-weight:400;font-size:36px;color:#222}
.h2 b{color:var(--blue);font-weight:600}
.about-title{left:600px;top:890px}
.about-text{left:600px;top:960px;width:490px;font-size:15px;line-height:25.7px;color:var(--muted);text-align:justify}
.about-btn{left:600px;top:1165px;width:161px;height:63px;font-size:18px}
.services{left:0;top:1323px;width:1200px;height:442px;background:linear-gradient(160deg,#153f91 0%,#133a86 60%,#0f3278 100%)}
.services-title{left:0;top:1405px;width:1200px;text-align:center;color:var(--white)}
.services-title b{color:var(--white)}
.card{top:1492px;width:210px;height:163px;background:var(--white);border-radius:6px;display:flex;flex-direction:column;align-items:center;justify-content:center;gap:12px;font-family:'Poppins',sans-serif;font-weight:600;font-size:18px;color:var(--blue);text-align:center;line-height:26px}
.connect-title{left:0;top:1850px;width:1200px;text-align:center}
.contact-item{left:176px;display:flex;align-items:center;gap:10px;font-size:17px;line-height:26px;color:#444}
.contact-item .circle-icon{width:44px;height:44px}
.field{background:var(--field);border:1px solid #d2d2d2;font-size:15px;color:#777;padding:0 12px;display:flex;align-items:center}
.submit{left:548px;top:2194px;width:127px;height:47px;font-size:16px;border-radius:3px}
.footer{left:0;top:2334px;width:1200px;height:399px;background:var(--black);color:var(--white)}
.footer-brand{left:166px;top:2410px;font-size:17px}
.footer-text{left:74px;top:2470px;width:330px;font-size:15px;line-height:26px}
.fhead{font-family:'Poppins',sans-serif;font-weight:600;font-size:17px;top:2418px}
.flist{top:2460px;font-size:15px;line-height:25.7px;list-style:none}
.news-input{left:911px;top:2459px;width:177px;height:34px;background:var(--white);font-size:12px;color:#888;padding:0 13px;display:flex;align-items:center}
.news-btn{left:912px;top:2515px;width:116px;height:40px;font-size:14px;border-radius:6px}
.socials{left:916px;top:2580px;display:flex;gap:16px}
.socials span{width:30px;height:30px;border-radius:50%;background:var(--blue)}
.socials span:nth-child(3){background:#d22}
.socials span:nth-child(4){background:#b8338e}
.rule{left:67px;top:2655px;width:1043px;height:1px;background:#555}
.copy{left:0;top:2671px;width:1200px;text-align:center;font-family:'Poppins',sans-serif;font-size:12px}
</style>
</head>
<body>
<div class="abs topbar"></div>

<header>
  <div class="abs brand site-brand"><span class="brand-mark"></span><span>VEL-CORA<br>SOLUTIONS</span></div>
  <nav class="abs nav">
    <a class="active" style="left:0">Home</a>
    <a style="left:79px">About Us</a>
    <a style="left:184px">what we do</a>
    <a style="left:311px">Blog</a>
    <a style="left:377px">contact us</a>
  </nav>
  <div class="abs phone-chip">
    <span class="circle-icon"><svg width="16" height="16" viewBox="0 0 24 24"><path fill="#fff" d="M6.6 10.8a15.1 15.1 0 0 0 6.6 6.6l2.2-2.2a1 1 0 0 1 1-.25 11.4 11.4 0 0 0 3.6.57 1 1 0 0 1 1 1V20a1 1 0 0 1-1 1A17 17 0 0 1 3 4a1 1 0 0 1 1-1h3.5a1 1 0 0 1 1 1c0 1.25.2 2.45.57 3.57a1 1 0 0 1-.25 1z"/></svg></span>
    <span>123 456 7890</span>
  </div>
</header>

<section>
  <div class="abs hero" role="img" aria-label="Hand holding a glowing tablet with a rising green stock chart"></div>
  <h1 class="abs hero-title">Vel-Cora Solutions</h1>
  <p class="abs hero-text">Vel Cora is an investment company put together by a group of seasoned business professionals who have come together to combine decades of success in the real estate development</p>
  <a class="abs btn hero-btn">Get Started</a>
  <div class="abs dots"><span class="on"></span><span></span><span></span></div>
</section>

<section>
  <div class="abs partner" style="left:142px">318 Build Inc.</div>
  <div class="abs partner" style="left:387px">GSH Dental<br>Services Ltd.</div>
  <div class="abs partner" style="left:632px">firmstance</div>
  <div class="abs partner" style="left:877px">Norvixa<br>Equipment Leasing</div>
</section>

<section>
  <div class="abs about-photo" role="img" aria-label="Businessman viewed from behind looking at a large financial data screen"></div>
  <h2 class="abs h2 about-title">About <b>Vel-Cora Solutions</b></h2>
  <p class="abs about-text">Lorem ipsum dolor sit amet, consectetur adipiscing elit, sed do eiusmod tempor incididunt ut labore et dolore magna aliqua. Ut enim ad minim veniam, quis nostrud exercitation ullamco laboris nisi ut aliquip ex ea commodo consequat. Duis aute irure dolor in reprehenderit in voluptate velit esse cillum dolore eu fugiat nulla pariatur. Excepteur sint occaecat cupidatat non proident, sunt in culpa qui officia deserunt mollit anim id est laborum</p>
  <a class="abs btn about-btn">Read More</a>
</section>

<section>
  <div class="abs services"></div>
  <h2 class="abs h2 services-title">what <b>we do</b></h2>
  <div class="abs card" style="left:128px">
    <svg width="56" height="66" viewBox="0 0 56 66" fill="none" stroke="#123f8f" stroke-width="2.5"><rect x="6" y="14" width="24" height="50"/><rect x="30" y="30" width="20" height="34"/><path d="M10 14V4h16v10M2 64h52"/><path d="M11 22h5M20 22h5M11 32h5M20 32h5M11 42h5M20 42h5M35 38h4M42 38h4M35 48h4M42 48h4"/></svg>
    <span>Real Estate<br>Development</span>
  </div>
  <div class="abs card" style="left:373px">
    <svg width="68" height="66" viewBox="0 0 68 66" fill="none" stroke="#123f8f" stroke-width="2.5"><circle cx="34" cy="14" r="11"/><path d="M29 25v5h10v-5M34 30v8M14 38h40M14 38v6M54 38v6"/><circle cx="14" cy="50" r="5"/><circle cx="34" cy="50" r="5"/><circle cx="54" cy="50" r="5"/><path d="M5 64a9 8 0 0 1 18 0M25 64a9 8 0 0 1 18 0M45 64a9 8 0 0 1 18 0"/></svg>
    <span>Management</span>
  </div>
  <div class="abs card" style="left:617px">
    <svg width="72" height="66" viewBox="0 0 72 66" fill="none" stroke="#123f8f" stroke-width="2.5"><rect x="4" y="18" width="46" height="28" rx="2"/><circle cx="27" cy="32" r="7"/><path d="M10 12l38-8 4 14"/><ellipse cx="58" cy="34" rx="10" ry="4"/><path d="M48 34v24c0 2 4 4 10 4s10-2 10-4V34M48 42c0 2 4 4 10 4s10-2 10-4M48 50c0 2 4 4 10 4s10-2 10-4"/></svg>
    <span>Financing</span>
  </div>
  <div class="abs card" style="left:861px">
    <svg width="68" height="66" viewBox="0 0 68 66" fill="none" stroke="#123f8f" stroke-width="2.5"><rect x="4" y="12" width="54" height="52"/><path d="M4 22h54"/><circle cx="54" cy="12" r="9" fill="#fff"/><path d="M54 7v10M49 12h10"/><path d="M10 30h10v10H10zM10 46h10v10H10zM40 30h12v10H40zM26 64V40h10v24M2 64h62"/></svg>
    <span>Medical Services</span>
  </div>
</section>

<section>
  <h2 class="abs h2 connect-title">Connect <b>With Us</b></h2>
  <div class="abs contact-item" style="top:1962px">
    <span class="circle-icon"><svg width="14" height="18" viewBox="0 0 14 18"><path fill="#fff" d="M7 0a7 7 0 0 0-7 7c0 5 7 11 7 11s7-6 7-11a7 7 0 0 0-7-7zm0 9.5A2.5 2.5 0 1 1 7 4.5a2.5 2.5 0 0 1 0 5z"/></svg></span>
    <span>Lorem ipsum dolor sit amet<br>consectetur adipisc</span>
  </div>
  <div class="abs contact-item" style="top:2035px">
    <span class="circle-icon"><svg width="16" height="16" viewBox="0 0 24 24"><path fill="#fff" d="M6.6 10.8a15.1 15.1 0 0 0 6.6 6.6l2.2-2.2a1 1 0 0 1 1-.25 11.4 11.4 0 0 0 3.6.57 1 1 0 0 1 1 1V20a1 1 0 0 1-1 1A17 17 0 0 1 3 4a1 1 0 0 1 1-1h3.5a1 1 0 0 1 1 1c0 1.25.2 2.45.57 3.57a1 1 0 0 1-.25 1z"/></svg></span>
    <span>+1 888 888 8888</span>
  </div>
  <div class="abs contact-item" style="top:2104px">
    <span class="circle-icon"><svg width="16" height="12" viewBox="0 0 16 12"><path fill="#fff" d="M0 0h16v2L8 7 0 2zM0 4l8 5 8-5v8H0z"/></svg></span>
    <span>info@velcorahealth.ca</span>
  </div>
  <div class="abs field" style="left:546px;top:1936px;width:230px;height:48px">First Name</div>
  <div class="abs field" style="left:794px;top:1936px;width:230px;height:48px">Last Name</div>
  <div class="abs field" style="left:546px;top:2003px;width:230px;height:48px">Email</div>
  <div class="abs field" style="left:794px;top:2003px;width:230px;height:48px">Phone</div>
  <div class="abs field" style="left:546px;top:2070px;width:478px;height:99px;align-items:flex-start;padding:12px 18px">Message</div>
  <a class="abs btn submit">SUBMIT</a>
</section>

<footer>
  <div class="abs footer"></div>
  <div class="abs brand footer-brand"><span class="brand-mark"></span><span>VEL-CORA<br>SOLUTIONS</span></div>
  <p class="abs footer-text">Lorem ipsum dolor sit amet, consectetur adipis cing elit, sed do eiusmod tempor incididunt ut labore et dolore magna aliqua. Ut enim ad min im veniam, quis nostrud exercitation ullamco laboris nisi ut aliquip ex ea</p>
  <h3 class="abs fhead" style="left:484px;color:#fff">Quick Links</h3>
  <ul class="abs flist" style="left:485px;color:#fff"><li>Home</li><li>About Us</li><li>What We Do</li><li>Blog</li><li>Contact Us</li></ul>
  <h3 class="abs fhead" style="left:647px;color:#fff">Our Services</h3>
  <ul class="abs flist" style="left:648px;color:#fff"><li>Real Estate Development</li><li>Management</li><li>Financing</li><li>Medical Services</li></ul>
  <h3 class="abs fhead" style="left:911px;color:#fff">Newsletters</h3>
  <div class="abs news-input">Enter The Email</div>
  <a class="abs btn news-btn">SUBSCRIBE</a>
  <div class="abs socials" aria-label="Social links"><span></span><span></span><span></span><span></span></div>
  <div class="abs rule"></div>
  <p class="abs copy" style="color:#fff">© Copyrights 2020 Vel Cora Solutions &nbsp;|&nbsp; All Rights Reserved</p>
</footer>
</body>
</html>
```